App Design - Career Prep Pal

We require an App Design for our new App called 'Hiring Helper'. This app is essentially an assistant to help Users prepare for job interviews, to help them get hired. <br/><br/>Users who download the App can view common Questions and Answers, save their favourite responses and also view common Interview Tips. <br/><br/>The vision for our App is for Users who are preparing for an interview (1 week before, 1 day before, even 1 hour before), are able to download, view and educate themselves on common questions and responses, and then be confident to land the job. <br/><br/>Our team has developed wireframes to help highlight what each screen should do and include. Please see attached document, which also highlights key requirements for the experience. Feel free to add/remove/edit what you see on these wireframes. Our preference is that you use Adobe XD please.<br/><br/>In terms of design guidelines, we want the experience to be simple, intuitive and 'memorable' to help Users to remember the questions/responses when they are in the interview. <br/><br/>The final design should communicate 'neat and clean professionalism'; we like the design of: jobvista net au<br/><br/>Thank you for reading! Good luck !

Target Market(s)

Professional job seekers

Font styles to use
Sans Serif

Colors

Designer to choose colors to be used in the design.

Requirements
Must have
• Please see my PixelGuild_UX file that I have uploaded
Nice to have
• Could you also please include some ideas on how we can incorporate Advertising into the app screens

```html
<!DOCTYPE html>
<html lang="en">
<head>
<meta charset="utf-8">
<title>Hiring Helper – View Question &amp; Responses</title>
<link rel="stylesheet" href="https://fonts.googleapis.com/css2?family=Nunito:wght@400;600;800;900&display=swap">
<style>
  :root {
    --canvas: #ffffff;
    --brand-blue: #1a4fc9;
    --brand-blue-deep: #1440b0;
    --brand-blue-light: #2a5fd6;
    --screen-bg: #e6e6e6;
    --card-bg: #efefef;
    --ink: #111111;
    --on-brand: #ffffff;
  }
  * { box-sizing: border-box; margin: 0; padding: 0; }
  html, body {
    width: 1200px; height: 800px; overflow: hidden;
    background: var(--canvas);
    font-family: "Nunito", sans-serif;
  }
  .stage {
    width: 1200px; height: 800px;
    display: flex; align-items: center; justify-content: center;
  }
  .screen {
    position: relative;
    width: 372px; height: 800px;
    background: var(--screen-bg);
    overflow: hidden;
  }
  .app-header {
    position: relative;
    height: 131px;
    color: var(--on-brand);
  }
  .header-photo {
    position: absolute; inset: 0;
    background: linear-gradient(160deg, var(--brand-blue-light) 0%, var(--brand-blue) 50%, var(--brand-blue-deep) 100%);
  }
  .status-bar {
    position: relative;
    display: flex; justify-content: space-between; align-items: center;
    height: 30px; padding: 8px 26px 0 34px;
    font-size: 10px; font-weight: 600;
  }
  .status-icons { display: flex; gap: 4px; align-items: center; }
  .title-row {
    position: relative;
    display: flex; align-items: center; gap: 14px;
    margin-top: 34px; padding-left: 12px;
  }
  .title-row h1 {
    font-size: 18.5px; font-weight: 900; letter-spacing: 0.2px;
  }
  .section-title {
    text-align: center;
    font-size: 16px; font-weight: 900;
    color: var(--ink);
    margin-top: 26px;
  }
  .question-list {
    list-style: none;
    position: absolute; left: 14px; right: 13px; top: 204px;
  }
  .question-card {
    display: flex; align-items: center;
    height: 103px; margin-bottom: 18px;
    background: var(--card-bg);
    border-radius: 4px;
    box-shadow: 0 1px 6px rgba(0,0,0,0.10);
    padding: 0 12px 0 13px;
  }
  .question-number {
    flex: none;
    width: 44px; height: 44px; border-radius: 50%;
    background: var(--brand-blue);
    color: var(--on-brand);
    display: flex; align-items: center; justify-content: center;
    font-size: 28px; font-weight: 400;
    box-shadow: 0 3px 6px rgba(0,0,0,0.25);
  }
  .question-text {
    margin-left: 13px;
    font-size: 7.6px; line-height: 13px; font-weight: 400;
    color: var(--ink);
  }
</style>
</head>
<body>
<main class="stage">
  <section class="screen">
    <header class="app-header">
      <div class="header-photo" role="img" aria-label="Blue-toned photo of people writing at a desk during an interview"></div>
      <div class="status-bar">
        <span class="status-time">9:41</span>
        <span class="status-icons">
          <svg width="12" height="8" viewBox="0 0 12 8"><rect x="0" y="6" width="2" height="2" fill="#fff"/><rect x="3" y="4" width="2" height="4" fill="#fff"/><rect x="6" y="2" width="2" height="6" fill="#fff"/><rect x="9" y="0" width="2" height="8" fill="#fff"/></svg>
          <svg width="11" height="8" viewBox="0 0 11 8"><path d="M0.5 2.8a7 7 0 0 1 10 0M2.3 4.6a4.4 4.4 0 0 1 6.4 0" stroke="#fff" stroke-width="1.3" fill="none"/><circle cx="5.5" cy="6.7" r="1.1" fill="#fff"/></svg>
          <svg width="16" height="8" viewBox="0 0 16 8"><rect x="0.5" y="0.5" width="13" height="7" rx="1.5" fill="#fff"/><rect x="14" y="2.5" width="1.5" height="3" fill="#fff"/></svg>
        </span>
      </div>
      <div class="title-row">
        <svg class="back-arrow" width="14" height="12" viewBox="0 0 14 12"><path d="M13 6H2M6.5 1.5 2 6l4.5 4.5" stroke="#fff" stroke-width="1.8" fill="none" stroke-linecap="round" stroke-linejoin="round"/></svg>
        <h1>VIEW QUESTION &amp; RESPONSES</h1>
      </div>
    </header>

    <h2 class="section-title">BEHAVIOURAL</h2>

    <ol class="question-list">
      <li class="question-card"><span class="question-number">1</span><p class="question-text">Lorem Ipsum is simply dummy text of the printing and typesetting industry. Lorem Ipsum has been the industry's standard dummy text ever since the 1500s, when an unknown printer took a galley of type and scrambled it to make a type specimen book. It has survived not only five centuries,</p></li>
      <li class="question-card"><span class="question-number">2</span><p class="question-text">Lorem Ipsum is simply dummy text of the printing and typesetting industry. Lorem Ipsum has been the industry's standard dummy text ever since the 1500s, when an unknown printer took a galley of type and scrambled it to make a type specimen book. It has survived not only five centuries,</p></li>
      <li class="question-card"><span class="question-number">3</span><p class="question-text">Lorem Ipsum is simply dummy text of the printing and typesetting industry. Lorem Ipsum has been the industry's standard dummy text ever since the 1500s, when an unknown printer took a galley of type and scrambled it to make a type specimen book. It has survived not only five centuries,</p></li>
      <li class="question-card"><span class="question-number">4</span><p class="question-text">Lorem Ipsum is simply dummy text of the printing and typesetting industry. Lorem Ipsum has been the industry's standard dummy text ever since the 1500s, when an unknown printer took a galley of type and scrambled it to make a type specimen book. It has survived not only five centuries,</p></li>
      <li class="question-card"><span class="question-number">5</span><p class="question-text">Lorem Ipsum is simply dummy text of the printing and typesetting industry. Lorem Ipsum has been the industry's standard dummy text ever since the 1500s, when an unknown printer took a galley of type and scrambled it to make a type specimen book. It has survived not only five centuries,</p></li>
    </ol>
  </section>
</main>
</body>
</html>
```